BOLD & MINIMALIST DESIGN NEEDED

We want a very bold but minimalistic business card design that is impactful and utilizes both sides of the business card. Our current logo is included for your use.

We want bold fonts and good use of negative space. We don't want the logo to overpower the design.

Target Market(s)

Professionals who are building new commercial buildings.

Industry/Entity Type

Construction

Contact Information for Business Card

Name, Title, email, office phone, cell phone, website

Font styles to use
Serif
Sans Serif

Requirements
Must have
• Bold design!

```html
<!DOCTYPE html>
<html lang="en">
<head>
<meta charset="utf-8">
<title>Ridgeline Design + Build – Business Card</title>
<link rel="stylesheet" href="https://fonts.googleapis.com/css2?family=Montserrat:wght@400;500;700;800&display=swap">
<style>
  :root {
    --page: #d9d9d9;
    --card: #161616;
    --white: #ffffff;
    --green: #6cc83a;
    --muted: #e6e6e6;
  }
  * { margin: 0; padding: 0; box-sizing: border-box; }
  html, body { width: 1200px; height: 874px; overflow: hidden; }
  body {
    background: var(--page);
    font-family: "Montserrat", Arial, sans-serif;
    position: relative;
  }
  .card {
    position: absolute;
    left: 250px;
    width: 700px;
    height: 400px;
    background: var(--card);
    border-radius: 22px;
    color: var(--white);
  }
  .card--front { top: 25px; }
  .card--back { top: 449px; }

  .brand {
    display: flex;
    flex-direction: column;
    align-items: center;
    color: var(--white);
    font-weight: 800;
  }
  .brand__row { display: flex; align-items: center; gap: 14px; }
  .brand__mark { background: var(--green); }
  .brand__name { letter-spacing: 1px; line-height: 1; }
  .brand__tag { letter-spacing: 9px; line-height: 1; margin-top: 10px; }

  .card--front .brand {
    position: absolute; inset: 0; justify-content: center;
  }
  .card--front .brand__mark { width: 30px; height: 30px; }
  .card--front .brand__name { font-size: 76px; }
  .card--front .brand__tag { font-size: 22px; padding-left: 9px; }

  .card--back .brand {
    position: absolute; left: 30px; top: 0; width: 330px; height: 100%; justify-content: center;
  }
  .card--back .brand__mark { width: 18px; height: 18px; gap: 10px; }
  .card--back .brand__name { font-size: 44px; }
  .card--back .brand__tag { font-size: 13px; letter-spacing: 6px; margin-top: 8px; padding-left: 6px; }

  .divider {
    position: absolute; left: 385px; top: 60px;
    width: 2px; height: 280px; background: var(--green);
  }
  .contact {
    position: absolute; left: 415px; top: 62px;
  }
  .contact__name {
    color: var(--green); font-weight: 700; font-size: 30px; letter-spacing: 1px; line-height: 1.1;
  }
  .contact__title {
    font-weight: 400; font-size: 16px; letter-spacing: 1px; margin-top: 4px; color: var(--muted);
  }
  .contact__address {
    font-size: 17px; line-height: 1.4; margin-top: 18px; color: var(--muted);
  }
  .contact__list { list-style: none; margin-top: 14px; }
  .contact__item {
    display: flex; align-items: center; gap: 10px;
    font-size: 17px; line-height: 1.6; color: var(--muted);
  }
  .contact__icon { width: 15px; height: 15px; flex: none; }
  .contact__icon * { fill: var(--green); }
</style>
</head>
<body>

<section class="card card--front" aria-label="Card front">
  <div class="brand">
    <div class="brand__row">
      <span class="brand__mark"></span>
      <span class="brand__name">RIDGELINE</span>
    </div>
    <span class="brand__tag">DESIGN + BUILD</span>
  </div>
</section>

<section class="card card--back" aria-label="Card back">
  <div class="brand">
    <div class="brand__row">
      <span class="brand__mark"></span>
      <span class="brand__name">RIDGELINE</span>
    </div>
    <span class="brand__tag">DESIGN + BUILD</span>
  </div>

  <div class="divider"></div>

  <div class="contact">
    <p class="contact__name">MARCUS HALE</p>
    <p class="contact__title">OWNER-CEO</p>
    <p class="contact__address">Your address, City<br>State, Zip 1234</p>
    <ul class="contact__list">
      <li class="contact__item">
        <svg class="contact__icon" viewBox="0 0 16 16" aria-hidden="true"><path d="M1 5c2-4 12-4 14 0l-3 2-2-2H6L4 7z"/><rect x="3" y="8" width="10" height="6" rx="1"/></svg>
        123 456 789
      </li>
      <li class="contact__item">
        <svg class="contact__icon" viewBox="0 0 16 16" aria-hidden="true"><path d="M4 1h8v14H4zM5.5 2.5v10h5v-10z"/></svg>
        123 456 789
      </li>
      <li class="contact__item">
        <svg class="contact__icon" viewBox="0 0 16 16" aria-hidden="true"><path d="M1 3h14v1.5L8 9 1 4.5z"/><path d="M1 6l7 4.5L15 6v7H1z"/></svg>
        info@yourmail.com
      </li>
      <li class="contact__item">
        <svg class="contact__icon" viewBox="0 0 16 16" aria-hidden="true"><path d="M8 1a7 7 0 1 0 0 14A7 7 0 0 0 8 1zm0 1.5a5.5 5.5 0 0 1 0 11 5.5 5.5 0 0 1 0-11z"/><rect x="2" y="7.3" width="12" height="1.4"/><rect x="7.3" y="2" width="1.4" height="12"/></svg>
        www.yourwebsite.com
      </li>
    </ul>
  </div>
</section>

</body>
</html>
```